Sophisticated, clean website reflecting my feminine, playful side to sell my abstract art,

I need a website no more than 3 pages to showcase my paintings, a little about me and some contact info. I do abstracts so looking for something a little edgy, yet feminine and current.
Updates

Hi there, These are some artists websites that I Iike: Marnelvoss.com (I like how airy it is) peterwallombry.com garethpolvens.com (I like how it scrolls) I'll need a place for a photo ( a headshot-i do not have it yet so I'll need to be able to upload that later) as well as an area for my bio. Also, it's important that I will be able to upload any new photos and descriptions easily so it should be user friendly. Lastly, I like in a sunny place so would like to have this seem upbeat and playful as that is how i like to paint. thanks-I'm trying to upload my photos now -

Target Market(s)

ppl ages 35-70 who want large scale art for their homes

Industry/Entity Type

art

Coding

Coded - Design and coding required

Number of Pages Required

3 page

Colors

Designer to choose colors to be used in the design.

Requirements
Must have
• photos of my art, a place for my bio, be easy to reach me. tasteful-nothing too "in your face" -my clients are pretty high end and organized. They like clean lines
Nice to have
• sophisticated background, muted tones in the back-similar clean font throughout-no cursive
Should not have
• too many dark areas. Too many blocks of color. Too serious.

```html
<!DOCTYPE html>
<html lang="en">
<head>
<meta charset="utf-8">
<title>Lena Marwick — Abstract Paintings</title>
<link rel="stylesheet" href="https://fonts.googleapis.com/css2?family=Anton&family=Barlow+Condensed:wght@500;600&family=Barlow:wght@300;400;500;600&display=swap">
<style>
  :root {
    --ink: #111111;
    --text: #3a3a3a;
    --cream: #f8f4ee;
    --white: #ffffff;
    --tan: #bdb38a;
    --shadow-tan: #b6ab98;
    --rule: #cfcfcf;
    --hero-a: #5f9a5a;
    --hero-b: #3f7f72;
    --art-a: #8b97ab;
    --art-b: #4a8a88;
    --display: "Anton", "Arial Narrow", sans-serif;
    --nav: "Barlow Condensed", "Arial Narrow", sans-serif;
    --body: "Barlow", Arial, sans-serif;
  }
  * { box-sizing: border-box; margin: 0; padding: 0; }
  html, body { width: 1200px; height: 3093px; overflow: hidden; }
  body { position: relative; background: var(--white); font-family: var(--body); color: var(--text); }

  /* Header */
  .site-header { position: absolute; left: 0; top: 0; width: 1200px; height: 165px; background: var(--white); }
  .brand { position: absolute; display: flex; align-items: center; gap: 16px; font-family: var(--display); color: var(--ink); letter-spacing: 2px; }
  .brand-mark { background: var(--ink); flex: none; }
  .brand--top { left: 0; width: 1200px; justify-content: center; top: 24px; font-size: 48px; line-height: 56px; }
  .brand--top .brand-mark { width: 50px; height: 50px; }
  .header-rule { position: absolute; left: 0; top: 100px; width: 1200px; height: 2px; background: var(--rule); }
  .main-nav { position: absolute; top: 118px; left: 0; width: 1200px; height: 30px; font-family: var(--nav); font-weight: 600; font-size: 23px; color: var(--ink); }
  .main-nav a { position: absolute; color: inherit; text-decoration: none; }
  .main-nav a.is-active::after { content: ""; position: absolute; left: 0; right: 0; bottom: -8px; height: 3px; background: var(--ink); }
  .social-dot { position: absolute; border-radius: 50%; background: var(--ink); }
  .nav-rule { position: absolute; left: 0; top: 164px; width: 1200px; height: 1px; background: var(--rule); }

  /* Hero */
  .hero { position: absolute; left: 0; top: 165px; width: 1200px; height: 628px; }
  .hero-image { position: absolute; inset: 0; background: linear-gradient(135deg, var(--hero-a), var(--hero-b)); }
  .hero-title { position: absolute; left: 0; top: 0; width: 1200px; height: 100%; text-align: center; color: var(--white); font-family: var(--display); letter-spacing: 3px; font-weight: 400; }
  .hero-title .kicker { position: absolute; left: 0; width: 100%; top: 228px; font-size: 46px; line-height: 50px; }
  .hero-title .name { position: absolute; left: 0; width: 100%; top: 277px; font-size: 72px; line-height: 80px; }
  .hero-arrow { position: absolute; top: 259px; width: 64px; height: 75px; background: rgba(40,40,40,.8); }
  .hero-arrow svg { position: absolute; left: 20px; top: 24px; }
  .dots { position: absolute; display: flex; gap: 9px; }
  .dots span { width: 12px; height: 12px; border-radius: 50%; background: var(--white); }
  .dots span.is-current { background: transparent; border: 2px solid var(--white); }

  /* About */
  .about { position: absolute; left: 0; top: 793px; width: 1194px; height: 664px; background: var(--cream); }
  .headshot-shadow { position: absolute; left: 148px; top: 147px; width: 375px; height: 387px; background: var(--shadow-tan); }
  .headshot { position: absolute; left: 115px; top: 138px; width: 392px; height: 387px; background: linear-gradient(180deg, #eeeeee, #e4e4e4); }
  .section-title { position: absolute; font-family: var(--display); color: var(--ink); letter-spacing: 2px; font-weight: 400; }
  .underline { position: absolute; height: 3px; background: var(--tan); }
  .about .section-title { left: 600px; top: 146px; font-size: 52px; line-height: 60px; }
  .about .underline { left: 601px; top: 212px; width: 64px; }
  .body-copy { position: absolute; font-size: 17.5px; line-height: 27.5px; font-weight: 300; color: var(--text); text-align: justify; }
  .about .p1 { left: 603px; top: 236px; width: 476px; }
  .about .p2 { left: 603px; top: 332px; width: 476px; }
  .btn-outline { position: absolute; left: 603px; top: 474px; width: 180px; height: 49px; border: 2px solid var(--ink); font-weight: 500; font-size: 17px; color: var(--text); display: flex; align-items: center; justify-content: center; letter-spacing: .5px; }

  /* Gallery */
  .gallery { position: absolute; left: 0; top: 1457px; width: 1200px; height: 777px; background: var(--white); }
  .gallery .section-title { left: 0; width: 1200px; text-align: center; top: 76px; font-size: 50px; line-height: 58px; }
  .gallery .underline { left: 563px; top: 137px; width: 64px; height: 2px; }
  .painting { position: absolute; left: 180px; top: 177px; width: 827px; height: 486px; }
  .painting-image { position: absolute; inset: 0; background: linear-gradient(90deg, var(--art-a), var(--art-b)); }
  .painting-frame { position: absolute; left: 13px; top: 12px; width: 801px; height: 462px; border: 2px solid rgba(255,255,255,.9); }
  .gallery-arrow { position: absolute; top: 373px; }

  /* Contact */
  .contact { position: absolute; left: 0; top: 2234px; width: 1200px; height: 668px; background: var(--cream); }
  .contact .section-title { left: 119px; top: 152px; font-size: 52px; line-height: 60px; }
  .contact .underline { left: 121px; top: 223px; width: 92px; }
  .contact .intro { left: 125px; top: 250px; width: 440px; font-size: 17.5px; line-height: 27px; text-align: left; }
  .info-icon { position: absolute; width: 66px; height: 66px; border-radius: 50%; background: var(--tan); display: flex; align-items: center; justify-content: center; }
  .info-label { position: absolute; font-size: 17px; font-weight: 400; color: var(--ink); letter-spacing: .3px; }
  .info-value { position: absolute; color: var(--ink); }
  .info-value.phone { font-weight: 600; font-size: 21px; }
  .info-value.email { font-weight: 400; font-size: 22px; }
  .contact-form { position: absolute; left: 595px; top: 144px; width: 478px; height: 388px; background: var(--white); border: 1px solid #dddddd; }
  .field { position: absolute; left: 32px; width: 412px; height: 48px; border: 1px solid #444; font-size: 14.5px; color: #333; padding: 14px 18px; }
  .btn-submit { position: absolute; left: 33px; top: 315px; width: 151px; height: 46px; background: var(--tan); color: var(--white); font-weight: 600; font-size: 17px; display: flex; align-items: center; justify-content: center; letter-spacing: .5px; }

  /* Footer */
  .site-footer { position: absolute; left: 0; top: 2902px; width: 1200px; height: 191px; background: var(--white); }
  .brand--foot { left: 147px; top: 25px; font-size: 31px; line-height: 44px; gap: 10px; letter-spacing: 1px; }
  .brand--foot .brand-mark { width: 42px; height: 42px; }
  .foot-nav { position: absolute; left: 0; width: 1200px; top: 34px; font-family: var(--nav); font-weight: 600; font-size: 21px; color: var(--ink); }
  .foot-nav a { position: absolute; color: inherit; text-decoration: none; white-space: nowrap; }
  .foot-rule { position: absolute; left: 130px; top: 101px; width: 993px; height: 2px; background: var(--rule); }
  .copyright { position: absolute; left: 0; width: 1200px; top: 136px; text-align: center; font-family: var(--nav); font-weight: 500; font-size: 12.5px; color: #444; letter-spacing: .3px; }
</style>
</head>
<body>

<header class="site-header">
  <div class="brand brand--top"><span class="brand-mark"></span><span>LENA MARWICK</span></div>
  <div class="header-rule"></div>
  <nav class="main-nav">
    <a class="is-active" href="#" style="left:300px">HOME</a>
    <a href="#" style="left:444px">ABOUT ME</a>
    <a href="#" style="left:626px">GALLERY</a>
    <a href="#" style="left:802px">CONTACT</a>
    <span class="social-dot" style="left:1020px;top:0;width:34px;height:34px"></span>
  </nav>
  <div class="nav-rule"></div>
</header>

<section class="hero">
  <div class="hero-image" role="img" aria-label="Featured abstract painting by the artist"></div>
  <h1 class="hero-title">
    <span class="kicker">WELCOME TO</span>
    <span class="name">LENA MARWICK</span>
  </h1>
  <div class="hero-arrow" style="left:0">
    <svg width="22" height="28" viewBox="0 0 22 28"><path d="M16 3 L5 14 L16 25" fill="none" stroke="#fff" stroke-width="4"/></svg>
  </div>
  <div class="hero-arrow" style="left:1145px;width:55px">
    <svg width="22" height="28" viewBox="0 0 22 28" style="left:16px"><path d="M6 3 L17 14 L6 25" fill="none" stroke="#fff" stroke-width="4"/></svg>
  </div>
  <div class="dots" style="left:544px;top:587px">
    <span class="is-current"></span><span></span><span></span><span></span><span></span><span></span><span></span>
  </div>
</section>

<section class="about">
  <div class="headshot-shadow"></div>
  <div class="headshot" role="img" aria-label="Headshot portrait of the artist"></div>
  <h2 class="section-title">ABOUT ME</h2>
  <div class="underline"></div>
  <p class="body-copy p1">Lorem ipsum dolor sit amet, consectetur adipiscing elit, sed do eiusmod tempor incididunt ut labore et dolore magna aliqua. Ut enim ad minim veniam, quis nostrud exercitation</p>
  <p class="body-copy p2">Duis aute irure dolor in reprehenderit in voluptate velit esse cillum dolore eu fugiat nulla pariatur. Excepteur sint occaecat cupidatat non proident, sunt in culpa qui officia deserunt mollit anim id est laborum.Sed ut perspiciatis unde</p>
  <a class="btn-outline">LEARN MORE</a>
</section>

<section class="gallery">
  <h2 class="section-title">PAINTING GALLERY</h2>
  <div class="underline"></div>
  <svg class="gallery-arrow" style="left:108px" width="28" height="54" viewBox="0 0 28 54"><path d="M26 2 L3 27 L26 52" fill="none" stroke="#222" stroke-width="2"/></svg>
  <svg class="gallery-arrow" style="left:1049px" width="28" height="54" viewBox="0 0 28 54"><path d="M2 2 L25 27 L2 52" fill="none" stroke="#222" stroke-width="2"/></svg>
  <div class="painting">
    <div class="painting-image" role="img" aria-label="Abstract painting from the gallery"></div>
    <div class="painting-frame"></div>
    <div class="dots" style="left:345px;top:442px">
      <span class="is-current"></span><span></span><span></span><span></span><span></span><span></span><span></span>
    </div>
  </div>
</section>

<section class="contact">
  <h2 class="section-title">CONTACT</h2>
  <div class="underline"></div>
  <p class="body-copy intro">Lorem ipsum dolor sit amet, consectetur adipiscing elit, sed do eiusmod tempor incididunt ut</p>

  <div class="info-icon" style="left:120px;top:336px">
    <svg width="34" height="34" viewBox="0 0 24 24"><path d="M6.6 10.8c1.4 2.8 3.8 5.1 6.6 6.6l2.2-2.2c.3-.3.7-.4 1-.2 1.1.4 2.3.6 3.6.6.6 0 1 .4 1 1V20c0 .6-.4 1-1 1C10.6 21 3 13.4 3 4c0-.6.4-1 1-1h3.5c.6 0 1 .4 1 1 0 1.3.2 2.5.6 3.6.1.3 0 .7-.2 1L6.6 10.8z" fill="#fff"/></svg>
  </div>
  <span class="info-label" style="left:203px;top:344px">PHONE NUMBER</span>
  <span class="info-value phone" style="left:202px;top:365px">(123) 456 7890</span>

  <div class="info-icon" style="left:120px;top:438px">
    <svg width="40" height="28" viewBox="0 0 40 28"><rect x="1.5" y="1.5" width="37" height="25" fill="none" stroke="#fff" stroke-width="2.5"/><path d="M2 2 L20 16 L38 2 M2 26 L15 12 M38 26 L25 12" fill="none" stroke="#fff" stroke-width="2.5"/></svg>
  </div>
  <span class="info-label" style="left:206px;top:443px">EMAIL US</span>
  <span class="info-value email" style="left:206px;top:462px">lenamarwick@info.com</span>

  <form class="contact-form">
    <div class="field" style="top:40px">Your Name</div>
    <div class="field" style="top:94px">Email address</div>
    <div class="field" style="top:149px">Phone Number</div>
    <div class="field" style="top:204px;height:90px">Message</div>
    <div class="btn-submit">SUBMIT</div>
  </form>
</section>

<footer class="site-footer">
  <div class="brand brand--foot"><span class="brand-mark"></span><span>LENA MARWICK</span></div>
  <nav class="foot-nav">
    <a href="#" style="left:491px">HOME</a>
    <a href="#" style="left:596px">ABOUT ME</a>
    <a href="#" style="left:736px">GALLERY</a>
    <a href="#" style="left:869px">CONTACT</a>
  </nav>
  <span class="social-dot" style="left:1047px;top:30px;width:33px;height:33px"></span>
  <div class="foot-rule"></div>
  <p class="copyright">© 2022 LENA MARWICK | ALL RIGHTS RESERVED</p>
</footer>

</body>
</html>
```